LEARN Business Skills so you can Earn a good living

size of the poster is 8”x 10.75" plus 0.25" bleed.
Please leave 1 inch on the bottoum for footer
I want a design a poster that will attract people's attention.
I appreciate a creative ad however the ad should not take away from being able to clearly read the text.
-I also appreciate a simple creative ad that is not too busy.
-you can use graphics, vectors, or pictures of real people.
-however, if you use real people it should be a white male that is wearing a white shirt and look like a professional person.

Target Market(s)

Potential young business people

Industry/Entity Type

education

Requirements
Must have
• easy to read the text
Nice to have
• I would like a "creative" simple ad that is easy to be read
Should not have
• pictures of women

```html
<!DOCTYPE html>
<html lang="en">
<head>
<meta charset="utf-8">
<title>Learn It to Earn It – Business Enrichment Course</title>
<link href="https://fonts.googleapis.com/css2?family=Montserrat:wght@400;700;800&family=Great+Vibes&display=swap" rel="stylesheet">
<style>
  :root{
    --stage:#8f8f8f;
    --band-dark:#34343d;
    --band-light:#60606f;
    --body-top:#41414f;
    --body-bottom:#2e2e37;
    --ghost:rgba(0,0,0,0.10);
    --ink:#ffffff;
    --footer:#ffffff;
    --photo-a:#d9d9de;
    --photo-b:#f4f4f6;
  }
  html,body{margin:0;padding:0;width:1200px;height:1200px;overflow:hidden;background:var(--stage);}
  .poster{
    position:absolute;left:162px;top:20px;width:877px;height:1160px;overflow:hidden;
    background:var(--footer);
    font-family:'Montserrat',Arial,sans-serif;color:var(--ink);
  }
  .hero-band{
    position:absolute;left:0;top:0;width:877px;height:548px;overflow:hidden;
    background:linear-gradient(100deg,var(--band-dark) 0%,var(--band-light) 100%);
  }
  .ghost-word{
    position:absolute;left:15px;margin:0;font-weight:800;font-size:390px;line-height:1;
    letter-spacing:-6px;color:var(--ghost);white-space:nowrap;
  }
  .ghost-word.row-one{top:-175px;}
  .ghost-word.row-two{top:164px;}
  .hero-photo{
    position:absolute;left:188px;top:15px;width:498px;height:533px;
    border-radius:40px 40px 0 0;
    background:linear-gradient(180deg,var(--photo-a) 0%,var(--photo-b) 100%);
  }
  .body-band{
    position:absolute;left:0;top:548px;width:877px;height:508px;
    background:linear-gradient(180deg,var(--body-top) 0%,var(--body-bottom) 100%);
  }
  .headline{
    position:absolute;margin:0;font-weight:800;font-size:153px;line-height:1;
    letter-spacing:-5.5px;white-space:nowrap;
    text-shadow:0 10px 18px rgba(0,0,0,0.35);
  }
  .headline.learn{left:93px;top:393px;}
  .headline.earn{left:179px;top:524px;}
  .headline-joiner{
    position:absolute;left:84px;top:560px;margin:0;
    font-family:'Great Vibes',cursive;font-size:120px;line-height:1;
    text-shadow:0 8px 14px rgba(0,0,0,0.35);
  }
  .course-title{
    position:absolute;left:80px;top:702px;margin:0;
    font-weight:700;font-size:48px;line-height:46px;letter-spacing:-0.3px;
  }
  .course-tagline{
    position:absolute;left:82px;top:850px;margin:0;
    font-weight:400;font-size:15px;line-height:19.5px;
  }
  .column-divider{
    position:absolute;left:438px;top:693px;width:1px;height:207px;background:var(--ink);
  }
  .benefits-intro{
    position:absolute;left:498px;top:702px;margin:0;font-weight:400;font-size:15px;line-height:20px;
  }
  .benefits{
    position:absolute;left:498px;top:724px;margin:0;
    font-weight:700;font-size:31px;line-height:41px;letter-spacing:-0.2px;
  }
  .topic-list{
    position:absolute;left:83px;top:938px;width:760px;margin:0;
    font-weight:700;font-size:11.1px;line-height:19.4px;text-transform:uppercase;white-space:nowrap;
  }
  .footer-space{
    position:absolute;left:0;top:1056px;width:877px;height:104px;background:var(--footer);
  }
</style>
</head>
<body>
  <main class="poster">
    <section class="hero-band">
      <p class="ghost-word row-one" aria-hidden="true">ARN</p>
      <p class="ghost-word row-two" aria-hidden="true">ARN</p>
      <div class="hero-photo" role="img" aria-label="Photo of a smiling young professional man in a white shirt holding an open laptop"></div>
    </section>
    <section class="body-band"></section>

    <h1 class="headline learn">LEARN IT</h1>
    <p class="headline-joiner">to</p>
    <p class="headline earn">EARN IT</p>

    <h2 class="course-title">Business<br>Enrichment<br>Course</h2>
    <p class="course-tagline">A proven success of helping<br>people in their livelihoods</p>

    <div class="column-divider"></div>

    <p class="benefits-intro">Business skills that will help you:</p>
    <p class="benefits">Get a quality job -<br>start / grow your<br>business-Increase<br>your salary</p>

    <p class="topic-list">
      Business Admiistration - Small Business Management -<br>
      Finance - Investments - Computers- Accounting - Sales&nbsp; Marketing - Project Management Interviewing<br>
      Skills - Business Law -Negotiation - Public Speaking - Import/Export - Information Technoloy -<br>
      Distribution - Marketing -&nbsp;&nbsp; Bookkeeping - Real Estate - Health Care-Management - Online Retail
    </p>

    <div class="footer-space"></div>
  </main>
</body>
</html>
```